Digital One Pager for Consulting Practice

I would like the essence of the content in my ppt consolidated into a one-pager. The one-pager will mainly be sent via email as a pdf and intended to excite and invite new clients and establish the credibility of my boutique high-end consulting firm. Infographics and symbols would be a plus. The target client should view the firm as providing premeir service. The client is getting a thought partner.

Target Market(s)

Large Medical Device Manufacturer Executives, Early-Stage Medical Device Manufacturer Executives, Partners at VC Firms

Industry/Entity Type

Medical Equipment

Colors
0355a3
f37122

Requirements
Must have
• Please match the color scheme in ppt. Please use the existing logo. I am very open to better graphics on the process. My photo does not need to be on the digital flyer. Hyper link to the website and email is needed.
Nice to have
• Infographics

```html
<!DOCTYPE html>
<html lang="en">
<head>
<meta charset="utf-8">
<title>Halden Ventures – One Pager</title>
<link href="https://fonts.googleapis.com/css2?family=Lato:wght@400;700;900&family=Nunito:wght@800;900&display=swap" rel="stylesheet">
<style>
:root{
  --blue:#0355a3;
  --blue-deep:#0a4a94;
  --orange:#f37122;
  --navy:#14213d;
  --white:#ffffff;
  --ink:#1c1c1c;
  --page-bg:#e9e6e1;
  --soft:#f2f3f5;
}
*{box-sizing:border-box;margin:0;padding:0}
html,body{width:1200px;height:1200px;overflow:hidden;background:var(--page-bg)}
body{font-family:"Lato",sans-serif;color:var(--ink)}
.flyer{position:absolute;left:186px;top:20px;width:828px;height:1160px;background:var(--white);box-shadow:0 4px 18px rgba(0,0,0,.18);overflow:hidden}
.brand{position:absolute;left:0;top:0;width:828px;height:118px;display:flex;align-items:center;justify-content:center;gap:14px}
.brand-dot{width:22px;height:22px;border-radius:50%;background:var(--orange)}
.brand-name{font-family:"Lato",sans-serif;font-weight:900;font-size:46px;letter-spacing:5px;color:var(--navy);text-transform:uppercase}

.experience{position:absolute;left:0;top:118px;width:828px;height:344px;background:linear-gradient(120deg,#0b5bb0 0%,var(--blue) 55%,#02478c 100%);color:var(--white)}
.experience h2{position:absolute;left:71px;top:12px;font-family:"Nunito",sans-serif;font-weight:900;font-size:24px}
.exp-list{position:absolute;left:38px;top:50px;width:520px;list-style:none}
.exp-item{position:relative;padding-left:33px;font-size:16.5px;line-height:21px;margin-bottom:21px}
.exp-item svg{position:absolute;left:0;top:2px}
.exp-sub{padding-left:33px;margin-top:-4px}
.exp-sub li{position:relative;list-style:none;font-size:16.5px;line-height:21px;margin-bottom:21px}
.exp-sub li::before{content:"";position:absolute;left:-15px;top:6px;border-left:8px solid var(--orange);border-top:4.5px solid transparent;border-bottom:4.5px solid transparent}
.portrait{position:absolute;left:552px;top:9px;width:265px;height:324px;border:2px solid #e6e9ef;background:radial-gradient(circle at 50% 40%,#6a6a6a,#2b2b2b 75%)}

.services-band{position:absolute;left:0;top:463px;width:828px;height:50px;background:var(--orange);color:var(--white);display:flex;align-items:center;justify-content:center;font-family:"Nunito",sans-serif;font-weight:900;font-size:31px;letter-spacing:.5px}
.services{position:absolute;left:0;top:513px;width:828px;height:573px;background:linear-gradient(180deg,#ffffff 0%,var(--soft) 60%,#eceef1 100%)}
.service{position:absolute}
.service .thumb{position:absolute;left:0;top:0}
.service h3{position:absolute;font-family:"Nunito",sans-serif;font-weight:900;font-size:17px;color:var(--orange);white-space:nowrap}
.service ul{position:absolute;list-style:none}
.service li{position:relative;padding-left:13px;font-size:15.5px;line-height:20px;margin-bottom:13px;white-space:nowrap}
.service li svg{position:absolute;left:0;top:6px}

.svc-strategy{left:29px;top:30px}
.svc-strategy .thumb{width:124px;height:133px;background:linear-gradient(135deg,#fafafa,#e4e4e4);border:1px solid #c9c9c9}
.svc-strategy h3{left:131px;top:20px}
.svc-strategy ul{left:131px;top:63px}

.svc-comms{left:492px;top:18px}
.svc-comms .thumb{width:120px;height:128px;background:linear-gradient(135deg,#8c939a,#3f4650)}
.svc-comms h3{left:137px;top:-2px}
.svc-comms ul{left:137px;top:46px}

.svc-interim{left:27px;top:217px}
.svc-interim .thumb{width:124px;height:138px;background:linear-gradient(135deg,#8e7a63,#c7cfd9)}
.svc-interim h3{left:134px;top:8px}
.svc-interim ul{left:134px;top:54px}

.svc-training{left:485px;top:217px}
.svc-training .thumb{width:120px;height:137px;background:linear-gradient(135deg,#4a2a1e,#8e3a22 60%,#2a1712)}
.svc-training h3{left:144px;top:3px}
.svc-training ul{left:144px;top:55px}

.process-frame{position:absolute;left:14px;top:920px;width:802px;height:180px;border:1.5px solid var(--navy);border-bottom:none;border-radius:26px 26px 0 0}
.process-title{position:absolute;left:304px;top:891px;width:265px;height:46px;border-radius:23px;background:var(--blue);color:var(--white);display:flex;align-items:center;justify-content:center;font-family:"Nunito",sans-serif;font-weight:900;font-size:24px}
.step{position:absolute;top:967px;width:109px;height:88px;border-radius:12px 0 12px 0;color:var(--white);font-family:"Nunito",sans-serif;font-weight:800;font-size:14.5px;line-height:19px;display:flex;align-items:center;padding:0 10px}
.step-orange{background:var(--orange);justify-content:center;text-align:center}
.step-blue{background:var(--blue)}
.arrow{position:absolute;top:996px}

.footer{position:absolute;left:0;top:1086px;width:828px;height:74px;background:var(--blue);color:var(--white);display:flex;align-items:center;font-size:16.5px}
.footer a{color:var(--white);text-decoration:none}
.contact{position:absolute;display:flex;align-items:center;gap:12px}
.contact-phone{left:30px}
.contact-mail{left:297px}
.contact-web{left:568px}
</style>
</head>
<body>
<main class="flyer">
  <header class="brand">
    <span class="brand-dot"></span>
    <span class="brand-name">Halden Ventures</span>
  </header>

  <section class="experience">
    <h2>Experience</h2>
    <ul class="exp-list">
      <li class="exp-item"><svg width="20" height="18" viewBox="0 0 20 18"><path d="M2 9l5 6L18 2" fill="none" stroke="#fff" stroke-width="2.2"/></svg>Over a decade @FDA (Former Deputy Division Director)</li>
      <li class="exp-item"><svg width="20" height="18" viewBox="0 0 20 18"><path d="M2 9l5 6L18 2" fill="none" stroke="#fff" stroke-width="2.2"/></svg>Expertise: Cardiovascular, Ophthalmology, General Hospital, Infection Control, Dental, Anesthesia, Respiratory</li>
      <li class="exp-item"><svg width="20" height="18" viewBox="0 0 20 18"><path d="M2 9l5 6L18 2" fill="none" stroke="#fff" stroke-width="2.2"/></svg>Vice President Regulatory Affairs / Quality Assurance @Corvane (Fortune 150 Company)</li>
    </ul>
    <ul class="exp-sub" style="position:absolute;left:38px;top:279px;top:279px">
    </ul>
    <ul class="exp-sub" style="position:absolute;left:38px;top:273px">
      <li>Initiated reorganization of department</li>
      <li>Led major compliance effort</li>
      <li>Successful FDA inspection (no observations)</li>
    </ul>
    <div class="portrait" role="img" aria-label="Portrait photo of the firm's founder"></div>
  </section>

  <div class="services-band">Services</div>
  <section class="services">
    <div class="service svc-strategy">
      <div class="thumb" role="img" aria-label="Strategy diagram sketch"></div>
      <h3>Regulatory Strategy</h3>
      <ul>
        <li><svg width="11" height="10" viewBox="0 0 11 10"><path d="M1 5l3 4 6-8" fill="none" stroke="#0355a3" stroke-width="2"/></svg>RAQA Organizational Structure</li>
        <li><svg width="11" height="10" viewBox="0 0 11 10"><path d="M1 5l3 4 6-8" fill="none" stroke="#0355a3" stroke-width="2"/></svg>Regulatory Pathway</li>
      </ul>
    </div>
    <div class="service svc-comms">
      <div class="thumb" role="img" aria-label="Team reviewing documents at a table"></div>
      <h3>FDA Communications</h3>
      <ul>
        <li><svg width="11" height="10" viewBox="0 0 11 10"><path d="M1 5l3 4 6-8" fill="none" stroke="#0355a3" stroke-width="2"/></svg>Deficiency Response</li>
        <li><svg width="11" height="10" viewBox="0 0 11 10"><path d="M1 5l3 4 6-8" fill="none" stroke="#0355a3" stroke-width="2"/></svg>Application Review</li>
      </ul>
    </div>
    <div class="service svc-interim">
      <div class="thumb" role="img" aria-label="Consultant speaking in an office"></div>
      <h3>Interim Executive Leadership</h3>
      <ul>
        <li><svg width="11" height="10" viewBox="0 0 11 10"><path d="M1 5l3 4 6-8" fill="none" stroke="#0355a3" stroke-width="2"/></svg>Compliance Remediation</li>
        <li><svg width="11" height="10" viewBox="0 0 11 10"><path d="M1 5l3 4 6-8" fill="none" stroke="#0355a3" stroke-width="2"/></svg>Accelerated Product Registration</li>
      </ul>
    </div>
    <div class="service svc-training">
      <div class="thumb" role="img" aria-label="Audience at a training session"></div>
      <h3>Training</h3>
      <ul>
        <li><svg width="11" height="10" viewBox="0 0 11 10"><path d="M1 5l3 4 6-8" fill="none" stroke="#0355a3" stroke-width="2"/></svg>FDA Communication</li>
        <li><svg width="11" height="10" viewBox="0 0 11 10"><path d="M1 5l3 4 6-8" fill="none" stroke="#0355a3" stroke-width="2"/></svg>MDR Reporting</li>
      </ul>
    </div>
  </section>

  <div class="process-frame"></div>
  <div class="process-title">Efficient Process</div>
  <div class="step step-orange" style="left:34px">Exploratory Call</div>
  <svg class="arrow" style="left:168px" width="38" height="28" viewBox="0 0 38 28"><path d="M2 14h32M22 3l12 11-12 11" fill="none" stroke="#0355a3" stroke-width="3.5"/></svg>
  <div class="step step-blue" style="left:255px">Regulatory Landscape</div>
  <svg class="arrow" style="left:398px" width="38" height="28" viewBox="0 0 38 28"><path d="M2 14h32M22 3l12 11-12 11" fill="none" stroke="#0355a3" stroke-width="3.5"/></svg>
  <div class="step step-orange" style="left:456px;justify-content:flex-start;text-align:left">Problem Statement</div>
  <svg class="arrow" style="left:609px" width="38" height="28" viewBox="0 0 38 28"><path d="M2 14h32M22 3l12 11-12 11" fill="none" stroke="#0355a3" stroke-width="3.5"/></svg>
  <div class="step step-blue" style="left:677px">Review &amp; Align on Deliverables</div>

  <footer class="footer">
    <div class="contact contact-phone">
      <svg width="28" height="28" viewBox="0 0 28 28"><circle cx="14" cy="14" r="12.5" fill="none" stroke="#fff" stroke-width="1.8"/><path d="M9.5 8.5c.8-.8 1.6-.6 2 .1l1.2 2c.3.6.1 1.1-.4 1.5l-.8.6c.6 1.5 1.8 2.8 3.3 3.5l.6-.8c.4-.5 1-.7 1.5-.4l2 1.2c.7.4.9 1.2.1 2-1.5 1.6-3.6 1.2-6.2-1.2-2.7-2.5-3.9-5.4-3.3-8.5z" fill="#fff"/></svg>
      <span>202.555.0148</span>
    </div>
    <div class="contact contact-mail">
      <svg width="28" height="20" viewBox="0 0 28 20"><rect x="1" y="1" width="26" height="18" fill="none" stroke="#fff" stroke-width="2"/><path d="M1 1l13 10L27 1M1 19l10-9M27 19l-10-9" fill="none" stroke="#fff" stroke-width="2"/></svg>
      <a href="mailto:info@haldenventures.com">info@haldenventures</a>
    </div>
    <div class="contact contact-web">
      <svg width="26" height="26" viewBox="0 0 26 26"><circle cx="13" cy="13" r="11" fill="none" stroke="#fff" stroke-width="1.8"/><ellipse cx="13" cy="13" rx="5" ry="11" fill="none" stroke="#fff" stroke-width="1.5"/><path d="M2 13h22M4 7h18M4 19h18" stroke="#fff" stroke-width="1.5"/></svg>
      <a href="https://www.haldenventures.com">www.haldenventures.com</a>
    </div>
  </footer>
</main>
</body>
</html>
```